Fenwick Grading LTD - website for irrigation & Landscape Lighting & Buried service wire

Looking for a website to help promote my business with Irrigation (installation, service, etc) and buried service wire/drainage solutions.

Commercial/Residential

Landscape lighting.

I’ll get photos in the trucks and trailers to upload as well maybe the machine as well.

Target Market(s)

Homeowners who want green grass and beautiful gardens. Beautiful landscape lighting

Industry/Entity Type

Irrigation systems and landscape lighting and buried service wire to homes and offering Drainage soltions.

Coding

Coded - Design and coding required

Number of Pages Required

4 page

Colors
F0912C
F2A743
F7CA91
FBE8D2
FDF5EE

Requirements
Must have
• was hoping to link up my email on fenwickgrading@mailbox-example.net with the website if possible.
Nice to have
• Page for Irrigation, page for landscape lighting, page buried service wire & drainage soltions.

```html
<!DOCTYPE html>
<html lang="en">
<head>
<meta charset="UTF-8">
<title>Fenwick Grading LTD</title>
<link href="https://fonts.googleapis.com/css2?family=Montserrat:wght@400;500;600;700&display=swap" rel="stylesheet">
<style>
:root{
  --orange:#F0912C;
  --orange-2:#F2A743;
  --peach:#F7CA91;
  --sand:#FBE8D2;
  --cream:#FDF5EE;
  --ink:#111111;
  --text:#333333;
  --muted:#555555;
  --card:#f5f5f5;
  --field:#f4f4f4;
  --line:#e2e2e2;
  --dark:#141414;
}
*{margin:0;padding:0;box-sizing:border-box}
html,body{width:1200px;height:3899px;overflow:hidden}
body{font-family:'Montserrat',sans-serif;color:var(--text);background:#fff;position:relative}
.abs{position:absolute}
a{color:inherit;text-decoration:none}

/* Header */
.site-header{position:absolute;left:0;top:0;width:1200px;height:70px;background:#fff;z-index:2}
.brand{position:absolute;left:141px;top:22px;font-weight:700;font-size:17px;color:var(--orange);letter-spacing:.5px;line-height:1.1}
.brand small{display:block;font-size:8px;letter-spacing:1.6px}
.main-nav{position:absolute;left:385px;top:27px;display:flex;gap:27px;font-size:13px;font-weight:500;color:var(--ink)}
.main-nav .active{color:var(--orange);border-bottom:2px solid var(--orange);padding-bottom:4px}
.header-cta{position:absolute;left:940px;top:18px;width:119px;height:34px;border-radius:17px;background:#fff;border:1px solid var(--peach);color:var(--orange);font-size:11px;font-weight:600;display:flex;align-items:center;justify-content:center;letter-spacing:.5px;z-index:3}

/* Hero */
.hero{position:absolute;left:0;top:70px;width:1200px;height:488px;background:var(--cream)}
.hero-photo{position:absolute;left:0;top:0;width:1200px;height:558px;z-index:1}
.hero-copy{position:absolute;left:141px;top:208px;z-index:2}
.hero-copy h1{font-size:30px;font-weight:500;color:var(--ink);line-height:47px}
.hero-copy h1 span{color:var(--orange)}
.hero-tag{margin-top:14px;border-left:2px solid var(--orange);padding:2px 0 2px 10px;font-size:12.5px;line-height:22px;color:var(--ink);width:420px}
.btn{display:inline-flex;align-items:center;justify-content:center;background:var(--orange);color:#fff;font-weight:600}
.hero-btn{margin-top:24px;width:161px;height:34px;border-radius:17px;font-size:11px;letter-spacing:.6px}

/* Section titles */
.section-title{position:absolute;left:0;width:1200px;text-align:center;font-size:40px;font-weight:700;color:var(--ink)}
.rule{position:absolute;left:570px;width:60px;height:2px;background:var(--orange)}

/* Services */
.services-intro{position:absolute;left:270px;top:738px;width:660px;text-align:center;font-size:15.5px;line-height:28px;color:var(--text)}
.service-card{position:absolute;top:812px;width:283px;height:323px;background:var(--card)}
.service-card .ph{width:265px;height:212px}
.service-card h3{font-size:17px;font-weight:600;color:var(--ink);margin:26px 0 0 20px}
.service-card .more{display:inline-block;margin:14px 0 0 20px;font-size:13px;color:var(--orange);font-weight:500;border-bottom:2px solid var(--orange);padding-bottom:3px}
.service-card.featured{background:#fff;height:376px;box-shadow:0 2px 10px rgba(0,0,0,.12);border:1px solid #ddd}
.service-card.featured h3{margin-top:20px;margin-left:24px}
.service-card.featured p{font-size:11.5px;line-height:20px;margin:10px 24px 0;color:var(--text)}
.service-card.featured .more{margin-top:4px;margin-left:27px}

/* About */
.about{position:absolute;left:0;top:1285px;width:1200px;height:626px}
.about-panel{position:absolute;left:608px;top:84px;width:450px;height:454px;background:rgba(10,10,10,.85);border:1px solid #bdbdbd;border-radius:10px;padding:52px 40px 0 40px;color:#fff}
.about-panel .kicker{font-size:20px;font-weight:600}
.about-panel h2{font-size:31px;font-weight:600;margin-top:16px}
.about-panel .bar{width:62px;height:2px;background:var(--orange);margin:20px 0 0 4px}
.about-panel p{font-size:11.5px;line-height:20.5px;margin-top:14px;padding-left:4px}
.about-panel .btn{margin:22px 0 0 4px;width:126px;height:42px;border-radius:3px;font-size:11.5px;font-weight:500}

/* Reviews */
.review-card{position:absolute;top:2118px;width:433px;height:257px;background:#fff;box-shadow:0 2px 12px rgba(0,0,0,.12);text-align:center}
.review-card::after{content:"";position:absolute;left:22px;right:22px;bottom:-3px;height:4px;background:var(--orange);border-radius:2px}
.avatar{position:absolute;left:177px;top:-31px;width:78px;height:78px;border-radius:50%;border:3px solid var(--orange);background:#fff;padding:4px}
.avatar span{display:block;width:100%;height:100%;border-radius:50%;background:linear-gradient(160deg,#c9a58a,#6b4e3c)}
.review-card h4{font-size:18px;font-weight:600;color:var(--ink);margin-top:64px}
.review-card p{font-size:11.5px;line-height:20.5px;margin:18px 36px 0;color:var(--text)}
.quote-mark{position:absolute;right:12px;bottom:14px}
.arrow{position:absolute;top:2224px;width:22px;height:28px}

/* Banner */
.banner{position:absolute;left:0;top:2474px;width:1200px;height:396px;text-align:center;color:#fff}
.banner h2{position:absolute;left:0;width:1200px;top:81px;font-size:30px;line-height:42px;font-weight:600}
.banner p{position:absolute;left:260px;width:680px;top:200px;font-size:11.5px;line-height:20px}
.banner .btn{position:absolute;left:541px;top:262px;width:118px;height:42px;border-radius:3px;font-size:11.5px;font-weight:500}

/* Contact */
.contact-card{position:absolute;left:227px;top:2961px;width:746px;height:418px;background:#fff;box-shadow:0 0 16px rgba(0,0,0,.08)}
.contact-card h2{position:absolute;top:48px;width:100%;text-align:center;font-size:33px;font-weight:700;color:var(--ink)}
.contact-card .sub{position:absolute;top:97px;width:100%;text-align:center;font-size:11.5px;color:var(--ink)}
.field{position:absolute;height:41px;background:var(--field);border:1px solid var(--line);display:flex;align-items:center;font-size:11.5px;color:var(--muted)}
.field .ico{width:40px;height:100%;border-right:1px solid var(--line);display:flex;align-items:center;justify-content:center}
.field .lbl{padding-left:12px;flex:1}
.field .lbl b{color:#e23a2a;font-weight:400}
.field.msg{align-items:flex-start}
.field.msg .ico{align-items:flex-start;padding-top:12px}
.field.msg .lbl{padding-top:14px}
.submit{position:absolute;left:56px;top:330px;width:637px;height:41px;border-radius:3px;font-size:11.5px;font-weight:500}

/* Footer */
.footer-shape{position:absolute;left:0;top:3468px;width:1200px;height:431px}
.footer-brand{position:absolute;left:0;top:3594px;width:1200px;text-align:center;color:var(--orange);font-weight:600;font-size:38px;letter-spacing:1px;line-height:1.1}
.footer-brand small{display:block;font-size:17px;letter-spacing:3px}
.footer-nav{position:absolute;left:0;top:3711px;width:1200px;display:flex;justify-content:center;gap:33px;font-size:11.5px;font-weight:600;color:#fff}
.footer-rule{position:absolute;left:141px;top:3752px;width:918px;height:1px;background:#333}
.contact-item{position:absolute;top:3773px;display:flex;align-items:center;gap:14px;color:#fff;font-size:12.5px;line-height:21px}
.contact-item .circ{width:34px;height:34px;border-radius:50%;background:#fff;border:3px solid var(--orange);display:flex;align-items:center;justify-content:center;flex:none}
.copyright{position:absolute;left:141px;top:3859px;font-size:11.5px;color:#ddd}
.socials{position:absolute;left:900px;top:3847px;display:flex;gap:7px}
.socials span{width:33px;height:33px;border-radius:50%;border:1.5px solid var(--orange);display:block}
</style>
</head>
<body>

<!-- Hero -->
<section class="hero"></section>
<svg class="hero-photo" viewBox="0 0 1200 558" role="img" aria-label="Photo of a sprinkler spraying water over a sunlit green lawn">
  <defs>
    <linearGradient id="lawn" x1="0" y1="0" x2="0" y2="1">
      <stop offset="0" stop-color="#e9e2b5"/>
      <stop offset=".35" stop-color="#b7bf6a"/>
      <stop offset=".7" stop-color="#5d8a2a"/>
      <stop offset="1" stop-color="#3d6a1b"/>
    </linearGradient>
  </defs>
  <path d="M858 0 C820 40 840 110 760 150 C690 185 640 230 648 300 C654 370 720 410 790 400 C860 392 900 430 930 480 C960 530 1040 560 1200 540 L1200 0 Z" fill="var(--orange)"/>
  <path d="M850 0 C812 40 830 105 752 145 C684 180 638 226 646 292 C652 358 714 398 784 390 C856 382 896 424 926 472 C956 520 1040 548 1200 528 L1200 0 Z" fill="url(#lawn)"/>
</svg>

<header class="site-header">
  <div class="brand">FENWICK GRADING<small>LTD</small></div>
  <nav class="main-nav">
    <a class="active">Home</a><a>Irrigation</a><a>Landscape Lighting</a><a>Buried Wire &amp; Drainage</a>
  </nav>
</header>
<a class="header-cta">CONTACT US</a>

<div class="hero-copy">
  <h1>Welcome To <span>Fenwick Grading</span><br>Your One-Stop Solution For<br>Home Improvement</h1>
  <div class="hero-tag">Expertise In Irrigation Systems, Landscape Lighting, Buried Service Wire And Drainage</div>
  <a class="btn hero-btn">GET A FREE QUOTE</a>
</div>

<!-- Services -->
<h2 class="section-title" style="top:650px">Our Services</h2>
<div class="rule" style="top:717px"></div>
<p class="services-intro">Lorem Ipsum is simply dummy text of the printing and typesetting industry. Lorem Ipsum has been the industry's standard dummy text ever since</p>

<article class="service-card" style="left:141px">
  <div class="ph" role="img" aria-label="Photo of a sprinkler watering lawn beside a gravel bed" style="background:linear-gradient(160deg,#a9a393,#7a9a4a 55%,#4f7d26)"></div>
  <h3>Irrigation Systems</h3>
  <a class="more">Learn More</a>
</article>
<article class="service-card featured" style="left:458px">
  <div class="ph" role="img" aria-label="Photo of a garden path lit by landscape lights at night" style="background:linear-gradient(160deg,#2e3a1c,#5e6a2e 50%,#1d2410)"></div>
  <h3>Landscape Lighting</h3>
  <p>Our landscape lighting solutions are designed to enhance the beauty and functionality of your outdoor space...</p>
  <a class="more">Learn More</a>
</article>
<article class="service-card" style="left:776px">
  <div class="ph" role="img" aria-label="Photo of a trench with buried service wire and drainage pipe" style="background:linear-gradient(160deg,#6b5a44,#5b6a3a 50%,#3a3a2c)"></div>
  <h3>Buried Wire &amp; Drainage</h3>
  <a class="more">Learn More</a>
</article>

<!-- About -->
<section class="about">
  <div class="abs" role="img" aria-label="Photo of a house with a trimmed lawn and garden beds" style="inset:0;background:linear-gradient(180deg,#7d8a7c 0%,#5d7440 40%,#4f7a22 70%,#5f9a2c 100%)"></div>
  <div class="about-panel">
    <div class="kicker">About</div>
    <h2>Fenwick Grading Ltd</h2>
    <div class="bar"></div>
    <p>Lorem ipsum dolor sit amet, consectetur adipiscing elit sed do eiusmod tempor incididunt ut labore et dolore magna aliqua Ut enim ad minim veniam quis</p>
    <p style="margin-top:8px">Lorem ipsum dolor sit amet, consectetur adipiscing elit sed do eiusmod tempor incididunt ut labore et dolore magna aliqua Ut enim ad minim veniam quis "Lorem ipsum dolor sit amet, consectetur adipiscing elit sed do eiusmod tempor incididunt ut labore et dolore magna aliqua</p>
    <a class="btn">Contact Us</a>
  </div>
</section>

<!-- Reviews -->
<h2 class="section-title" style="top:1998px;font-size:33px">Customer Reviews</h2>
<div class="rule" style="top:2061px"></div>

<svg class="arrow" style="left:136px" viewBox="0 0 22 28"><path d="M14 0 L2 14 L14 28" fill="#fff" stroke="var(--orange)" stroke-width="2"/><path d="M12 11 L9 14 L12 17" fill="none" stroke="#333" stroke-width="1.5"/></svg>
<article class="review-card" style="left:144px">
  <div class="avatar" role="img" aria-label="Customer portrait"><span></span></div>
  <h4>Marcus Hale</h4>
  <p>Lorem Ipsum is simply dummy text of the printing and typesetting industry. Lorem Ipsum has been the industry's standard dummy text ever since the 1500s, when an unknown printer took a galley of type and scrambledstandard dummy text ever since standard dummy text ever since</p>
  <svg class="quote-mark" width="42" height="32" viewBox="0 0 42 32"><path d="M2 2h16v16l-6 12H6l5-12H2zM24 2h16v16l-6 12h-6l5-12h-9z" fill="none" stroke="#d8d8d8" stroke-width="2"/></svg>
</article>
<article class="review-card" style="left:625px">
  <div class="avatar" role="img" aria-label="Customer portrait"><span></span></div>
  <h4>Nadia Brooks</h4>
  <p>Lorem Ipsum is simply dummy text of the printing and typesetting industry. Lorem Ipsum has been the industry's standard dummy text ever since the 1500s, when an unknown printer took a galley of type and scrambled standard dummy text ever since standard dummy text ever since</p>
  <svg class="quote-mark" width="42" height="32" viewBox="0 0 42 32"><path d="M2 2h16v16l-6 12H6l5-12H2zM24 2h16v16l-6 12h-6l5-12h-9z" fill="none" stroke="#d8d8d8" stroke-width="2"/></svg>
</article>
<svg class="arrow" style="left:1042px" viewBox="0 0 22 28"><path d="M8 0 L20 14 L8 28" fill="#fff" stroke="var(--orange)" stroke-width="2"/><path d="M10 11 L13 14 L10 17" fill="none" stroke="#333" stroke-width="1.5"/></svg>

<!-- Banner -->
<section class="banner">
  <div class="abs" role="img" aria-label="Photo of a garden lawn with sprinklers at dusk" style="inset:0;background:linear-gradient(180deg,#233226 0%,#1c2c22 50%,#24381f 100%)"></div>
  <h2>Expertise In Irrigation Systems, Landscape<br>Lighting, Buried Wire And Drainage Solutions</h2>
  <p>Lorem ipsum dolor sit amet, consectetuer adipiscing elit, sed diam nonummy nibh euismod tincidunt ut laoreet dolore magna aliquam erat volutpat. Ut wisi enim ad minim veniam, quis nostrud exerci tation.</p>
  <a class="btn">Contact Us</a>
</section>

<!-- Contact -->
<section class="contact-card">
  <h2>Contact Us</h2>
  <div class="sub">Lorem ipsum dolor sit amet consectetuer adipiscing elit</div>
  <div class="field" style="left:56px;top:126px;width:312px"><span class="ico"><svg width="14" height="14" viewBox="0 0 14 14"><circle cx="7" cy="4" r="3.2" fill="#bbb"/><path d="M1 14c0-4 3-6 6-6s6 2 6 6z" fill="#bbb"/></svg></span><span class="lbl">First Name<b>*</b></span></div>
  <div class="field" style="left:381px;top:126px;width:312px"><span class="ico"><svg width="14" height="14" viewBox="0 0 14 14"><path d="M1 7 13 1 10 13 7 9z" fill="#bbb"/></svg></span><span class="lbl">Email Address<b>*</b></span></div>
  <div class="field" style="left:56px;top:182px;width:312px"><span class="ico"><svg width="14" height="14" viewBox="0 0 14 14"><path d="M3 1 6 4 4.5 6C5.5 8 6.5 9 8 9.5L10 8l3 3-2 2C6 13 1 8 1 3z" fill="#bbb"/></svg></span><span class="lbl">Telephone<b>*</b></span></div>
  <div class="field" style="left:381px;top:182px;width:312px"><span class="ico"><svg width="14" height="14" viewBox="0 0 14 14"><rect x="1.5" y="2" width="9" height="11" fill="none" stroke="#bbb" stroke-width="1.5"/><path d="M5 9 12 2" stroke="#bbb" stroke-width="1.8"/></svg></span><span class="lbl">inquiry For<b>*</b></span><svg style="margin-right:30px" width="12" height="7" viewBox="0 0 12 7"><path d="M1 1 6 6 11 1" fill="none" stroke="#aaa" stroke-width="1.2"/></svg></div>
  <div class="field msg" style="left:56px;top:237px;width:637px;height:79px"><span class="ico"><svg width="15" height="13" viewBox="0 0 15 13"><path d="M1 1h9v6H5l-3 2V7H1z M11 4h3v6h-1v2l-3-2H6V8h5z" fill="#bbb"/></svg></span><span class="lbl">Messages</span></div>
  <a class="btn submit">Submit Now</a>
</section>

<!-- Footer -->
<svg class="footer-shape" viewBox="0 0 1200 431" preserveAspectRatio="none">
  <polygon points="0,80 600,4 1200,80 1200,431 0,431" fill="var(--dark)"/>
  <polyline points="60,72 600,4 1140,72" fill="none" stroke="var(--orange)" stroke-width="3"/>
</svg>
<div class="footer-brand">FENWICK GRADING<small>LTD</small></div>
<nav class="footer-nav"><a>Home</a><a>Irrigation</a><a>Landscape Lighting</a><a>Buried Wire &amp; Drainage</a><a>Contact Us</a></nav>
<div class="footer-rule"></div>

<div class="contact-item" style="left:201px">
  <span class="circ"><svg width="12" height="15" viewBox="0 0 12 15"><path d="M6 0a6 6 0 0 0-6 6c0 4 6 9 6 9s6-5 6-9a6 6 0 0 0-6-6z" fill="#222"/><circle cx="6" cy="6" r="2" fill="#fff"/></svg></span>
  <div>123, Building Name, Street<br>City, State XY 123456</div>
</div>
<div class="contact-item" style="left:506px">
  <span class="circ"><svg width="14" height="14" viewBox="0 0 14 14"><path d="M3 1 6 4 4.5 6C5.5 8 6.5 9 8 9.5L10 8l3 3-2 2C6 13 1 8 1 3z" fill="#222"/></svg></span>
  <div>Phone<br>123-456-7890</div>
</div>
<div class="contact-item" style="left:738px">
  <span class="circ"><svg width="14" height="10" viewBox="0 0 14 10"><rect width="14" height="10" rx="1" fill="#222"/><path d="M1 1 7 6 13 1" fill="none" stroke="#fff" stroke-width="1.2"/></svg></span>
  <div>E-Mail<br>fenwickgrading@mailbox-example.net</div>
</div>

<div class="copyright">© 2024 Fenwick Grading Ltd . All Rights Reserved.</div>
<div class="socials"><span></span><span></span><span></span><span></span></div>

</body>
</html>
```